Boutique custom software development company needs new business card

Our nearly 20 year old custom software development company would like to better include the fact that we are now providing Bitcoin services. These new services are B2B include education (how to acquire and securely hold Bitcoin) and integrating Bitcoin payments into existing ecommerce sites or other existing systems. Please keep the card clean and simple. Attached is our current design and some other files. vextorial.com

Target Market(s)

businesses owners interested in long term relationship

Industry/Entity Type

Custom software development and Bitcoin

Contact Information for Business Card

Dale Parker, dale@vextorial.com, vextorial.com, (888) 555-VXTRL

Font styles to use
Other font styles liked:
• monospace

Requirements
Must have
• double-sided
Nice to have
• clean and simple
Should not have
• physical address

```html
<!DOCTYPE html>
<html lang="en">
<head>
<meta charset="utf-8">
<title>Vextorial Business Card</title>
<link rel="stylesheet" href="https://fonts.googleapis.com/css2?family=Montserrat:wght@300;400;700&family=Oswald:wght@500&display=swap">
<style>
  :root {
    --page-bg: #e9eaec;
    --brand-blue: #3d73b9;
    --brand-orange: #f07a1f;
    --card-white: #ffffff;
    --text-grey: #5d6168;
    --rule-blue: #4f7fc0;
  }
  * { margin: 0; padding: 0; box-sizing: border-box; }
  html, body {
    width: 1200px; height: 900px; overflow: hidden;
    background: var(--page-bg);
    font-family: "Montserrat", sans-serif;
  }
  .card-sheet {
    width: 1200px; height: 900px;
    display: flex; flex-direction: column; align-items: center;
    justify-content: center; gap: 40px;
  }
  .card {
    position: relative;
    width: 700px; height: 400px;
    border-radius: 18px;
    box-shadow: 0 4px 14px rgba(0,0,0,0.12);
    overflow: hidden;
  }
  /* Front */
  .card-front {
    background: var(--brand-blue);
    display: flex; align-items: center; justify-content: center;
  }
  .brand-block { margin-top: -30px; }
  .brand-name {
    font-weight: 700; font-size: 64px; letter-spacing: 1px;
    color: var(--card-white); line-height: 1;
  }
  .brand-tagline {
    margin-top: 12px; font-weight: 400; font-size: 22px;
    color: var(--card-white); letter-spacing: 0.2px;
  }
  /* Back */
  .card-back { background: var(--card-white); }
  .identity {
    position: absolute; left: 0; right: 0; top: 145px;
    display: flex; align-items: center; justify-content: center;
  }
  .person { text-align: right; padding-right: 20px; }
  .person-name {
    font-family: "Oswald", sans-serif; font-weight: 500;
    font-size: 44px; line-height: 1; letter-spacing: 1px;
    white-space: nowrap;
  }
  .name-first { color: var(--brand-orange); }
  .name-last { color: var(--brand-blue); }
  .person-title {
    margin-top: 4px; font-weight: 300; font-size: 20px;
    color: var(--text-grey); letter-spacing: 1px;
  }
  .divider {
    width: 1.5px; height: 90px; background: var(--rule-blue); flex: none;
  }
  .contact-list {
    list-style: none; padding-left: 20px;
    font-size: 16px; color: var(--text-grey); font-weight: 400;
  }
  .contact-list li {
    display: flex; align-items: center; gap: 9px; line-height: 1.7;
    white-space: nowrap;
  }
  .contact-icon { width: 13px; height: 13px; flex: none; }
  .web-name { color: var(--brand-blue); }
  .services {
    position: absolute; left: 0; right: 0; bottom: 70px;
    text-align: center; font-size: 18px; color: var(--text-grey);
    letter-spacing: 0.5px;
  }
  .services-accent { color: var(--brand-orange); }
</style>
</head>
<body>
<main class="card-sheet">
  <section class="card card-front" aria-label="Card front">
    <div class="brand-block">
      <div class="brand-name">VEXTORIAL</div>
      <div class="brand-tagline">developer of custom applications</div>
    </div>
  </section>

  <section class="card card-back" aria-label="Card back">
    <div class="identity">
      <div class="person">
        <div class="person-name"><span class="name-first">DALE</span> <span class="name-last">PARKER</span></div>
        <div class="person-title">DIRECTOR</div>
      </div>
      <div class="divider"></div>
      <ul class="contact-list">
        <li>
          <svg class="contact-icon" viewBox="0 0 24 24" fill="var(--brand-blue)"><path d="M6.6 10.8a15.1 15.1 0 0 0 6.6 6.6l2.2-2.2c.3-.3.7-.4 1-.2 1.1.4 2.3.6 3.6.6.6 0 1 .4 1 1V20c0 .6-.4 1-1 1C10.6 21 3 13.4 3 4c0-.6.4-1 1-1h3.5c.6 0 1 .4 1 1 0 1.3.2 2.5.6 3.6.1.3 0 .7-.2 1z"/></svg>
          (888) 555-VXTRL
        </li>
        <li>
          <svg class="contact-icon" viewBox="0 0 24 24" fill="none" stroke="var(--brand-blue)" stroke-width="2"><rect x="3" y="5" width="18" height="14" rx="1"/><path d="M3 6l9 7 9-7"/></svg>
          dale@vextorial.com
        </li>
        <li>
          <svg class="contact-icon" viewBox="0 0 24 24" fill="none" stroke="var(--brand-blue)" stroke-width="1.8"><circle cx="12" cy="12" r="9"/><path d="M3 12h18M12 3c3 3 3 15 0 18M12 3c-3 3-3 15 0 18"/></svg>
          <span>www.<span class="web-name">vextorial</span>.com</span>
        </li>
      </ul>
    </div>
    <p class="services">Custom Software <span class="services-accent">·</span> Bitcoin Payments <span class="services-accent">·</span> Bitcoin Education</p>
  </section>
</main>
</body>
</html>
```